MRT Property - Business Cards

Looking for a business card & general letterhead, signage etc design for our new logo.

Colours:
000a20
0056a2
00b5ef
0088ce
68cef2

Fonts:
Poppins
Karla

Please keep look and feel of new brand - example in the zip package I sent.

```html
<!DOCTYPE html>
<html lang="en">
<head>
<meta charset="utf-8">
<title>MRT Property – Business Cards</title>
<link rel="stylesheet" href="https://fonts.googleapis.com/css2?family=Poppins:wght@300;400;500;600;700&display=swap">
<style>
  :root {
    --stage: #222222;
    --card-navy: #0f1328;
    --brand-blue: #0d5aa7;
    --mid-blue: #0088ce;
    --sky: #00b5ef;
    --light-sky: #68cef2;
    --white: #ffffff;
  }
  * { margin: 0; padding: 0; box-sizing: border-box; }
  html, body {
    width: 1200px; height: 780px; overflow: hidden;
    background: var(--stage);
    font-family: "Poppins", sans-serif;
  }
  .stage {
    position: relative; width: 1200px; height: 780px;
    display: flex; align-items: center; justify-content: center; gap: 40px;
  }
  .card {
    position: relative; width: 540px; height: 310px;
    background: var(--card-navy);
    overflow: hidden;
    box-shadow: 0 14px 30px rgba(0,0,0,0.45);
  }
  .wordmark {
    position: absolute;
    color: var(--brand-blue);
    font-weight: 700;
    letter-spacing: 1px;
    white-space: nowrap;
    line-height: 1;
  }
  .card-front .wordmark { top: 52px; right: 40px; font-size: 34px; }
  .card-back .wordmark { bottom: 44px; right: 44px; font-size: 30px; }

  .holder { position: absolute; left: 40px; top: 102px; text-align: right; }
  .holder-name { color: var(--brand-blue); font-size: 27px; font-weight: 500; line-height: 1.1; }
  .holder-name strong { font-weight: 600; }
  .holder-role { color: var(--white); font-size: 13px; font-weight: 400; margin-top: 2px; }

  .divider {
    position: absolute; left: 262px; top: 118px; width: 1px; height: 84px;
    background: var(--brand-blue);
  }
  .contacts { position: absolute; left: 282px; top: 122px; list-style: none; }
  .contacts li {
    display: flex; align-items: center; gap: 8px;
    color: var(--white); font-size: 13.5px; font-weight: 400; line-height: 26px;
  }
  .contacts svg { width: 14px; height: 14px; flex: none; }

  .band { position: absolute; left: 0; top: 0; width: 540px; height: 310px; }
  .address {
    position: absolute; left: 26px; bottom: 18px;
    color: var(--white); font-size: 13px; font-weight: 400; letter-spacing: 0.2px;
  }
</style>
</head>
<body>
<main class="stage">
  <section class="card card-front" aria-label="Front of business card">
    <svg class="band" viewBox="0 0 540 310" aria-hidden="true">
      <path d="M0,222 C130,282 360,280 540,252 L540,310 L0,310 Z" fill="var(--brand-blue)"/>
      <path d="M18,204 C150,268 360,266 512,242" fill="none" stroke="var(--light-sky)" stroke-width="3" stroke-linecap="round"/>
    </svg>

    <div class="wordmark">MRT PROPERTY</div>

    <div class="holder">
      <p class="holder-name"><strong>Liam</strong> Carver</p>
      <p class="holder-role">Director</p>
    </div>

    <div class="divider"></div>

    <ul class="contacts">
      <li>
        <svg viewBox="0 0 24 24"><path fill="var(--sky)" d="M6.6 10.8a15.1 15.1 0 0 0 6.6 6.6l2.2-2.2a1 1 0 0 1 1-.25 11.4 11.4 0 0 0 3.6.57 1 1 0 0 1 1 1V20a1 1 0 0 1-1 1A17 17 0 0 1 3 4a1 1 0 0 1 1-1h3.5a1 1 0 0 1 1 1c0 1.25.2 2.45.57 3.57a1 1 0 0 1-.25 1z"/></svg>
        +61 2 5550 0142
      </li>
      <li>
        <svg viewBox="0 0 24 24"><circle cx="12" cy="12" r="9" fill="none" stroke="var(--sky)" stroke-width="2"/><path d="M3 12h18M12 3c3 3 3 15 0 18M12 3c-3 3-3 15 0 18" fill="none" stroke="var(--sky)" stroke-width="1.6"/></svg>
        www.mrtproperty.com.au
      </li>
      <li>
        <svg viewBox="0 0 24 24"><rect x="3" y="6" width="18" height="13" rx="1.5" fill="var(--sky)"/><path d="M3.5 7l8.5 6.5L20.5 7" fill="none" stroke="var(--card-navy)" stroke-width="1.6"/></svg>
        info@mrtproperty.com.au
      </li>
    </ul>

    <p class="address">Suite 4.12, Level 4, 18 Harbourline Road, Westbrook NSW 2190</p>
  </section>

  <section class="card card-back" aria-label="Back of business card">
    <div class="wordmark">MRT PROPERTY</div>
  </section>
</main>
</body>
</html>
```